Vintage poster/postcard for 2011 New Years Eve event with theme 'Nouveau Cirque'

I have had a major change of mind since the last brief due to my original requirements being too specific. I hope this new brief allows more scope for the designers and I am extending the deadline by 7 days.

For the first time my new business 'Quillmere Gala' is planning an exciting, large scale New Years Eve fundraising event in Hobart Tasmania, Australia. The unique and eclectic theme of the party is 'Nouveau Cirque' (french for contemporary circus). I require a vintage style poster design (similar to a traditional french advertising poster) that can double as a postcard invitation so it must look good on a smaller scale as well.
Updates

Project Deadline Extended
Reason: My original brief was very specific and I now realise very limiting for the designers. I have changed my mind with the look I want for the vintage poster (more along the lines of the traditional french advertising posters of old) and therefore would like to allow designers extra time to submit a design. Thank you. Jun Okafor Quillmere Gala

Target Market(s)

25-50 yr old professionals prepared to pay premium price for a quality, fresh & fun NYE experience while giving to charity.

Industry/Entity Type

Advertising

Requirements
Must have
• - A heading that reads: Quillmere Gala proudly presents
Nouveau Cirque
- Text that includes: 2011 New Years Eve Extravanaganza Saturday 31st December and find out more at "www.quillmeregala-example.com
- A strip left blank at the bottom to include my business logo and others sponsors
- Classic french vintage poster design
- - Plenty of colour but not too fluro
- Something that looks good enough to be framed or sent to a friend
Should not have
• - Picture of Eiffel Tower or any other specific French references
- Any animals

```html
<!DOCTYPE html>
<html lang="en">
<head>
<meta charset="utf-8">
<title>Quillmere Gala – Nouveau Cirque</title>
<link rel="stylesheet" href="https://fonts.googleapis.com/css2?family=Cinzel:wght@700;900&family=Sancreek&family=Arimo:wght@700&display=swap">
<style>
  :root {
    --parchment: #d8a862;
    --cream: #f7e8c6;
    --red: #c61f1c;
    --red-deep: #7e1210;
    --performer: #e2412f;
    --ink: #2a130e;
    --gold: #c99a50;
    --strip: #0f0b0a;
  }
  * { margin: 0; padding: 0; box-sizing: border-box; }
  html, body { width: 849px; height: 1200px; overflow: hidden; background: #fff; }
  .poster {
    position: relative; width: 849px; height: 1200px; overflow: hidden;
    background: var(--parchment);
  }
  .fill { position: absolute; }
  .side-pattern {
    top: 0; bottom: 0; width: 80px;
    background: linear-gradient(180deg, #d9ab66, #b98242 50%, #d9ab66);
  }
  .side-pattern.left { left: 0; }
  .side-pattern.right { right: 0; }
  .stage-panel {
    left: 58px; right: 58px; top: 58px; bottom: 40px;
    background: radial-gradient(ellipse at 50% 40%, #d8342a 0%, var(--red) 45%, var(--red-deep) 100%);
  }
  .crest {
    left: 150px; right: 150px; top: 20px; height: 150px;
    border-radius: 50% 50% 0 0 / 100% 100% 0 0;
    background: radial-gradient(ellipse at 50% 100%, #b52a20, #8a3a1c 60%, var(--gold) 100%);
  }
  .figure {
    top: 300px; width: 150px; height: 480px;
    border-radius: 75px 75px 10px 10px;
    background: linear-gradient(180deg, rgba(226,65,47,0.85) 0%, rgba(200,30,27,0.7) 60%, rgba(200,30,27,0) 100%);
  }
  .figure.left { left: 84px; }
  .figure.right { right: 84px; }
  .curtain {
    left: 174px; width: 501px; top: 680px; height: 420px;
    background: linear-gradient(90deg, #3b1a12 0%, #a31816 18%, #d22a22 50%, #a31816 82%, #3b1a12 100%);
  }
  .frame-lines { position: absolute; inset: 0; }
  .plaque {
    position: absolute; left: 210px; top: 214px; width: 429px; height: 120px;
    border-radius: 60px; background: var(--ink);
    border: 6px solid var(--gold);
    text-align: center; color: var(--cream);
    font-family: "Cinzel", serif; font-weight: 700; white-space: nowrap;
  }
  .plaque .host { display: block; font-size: 36px; line-height: 44px; margin-top: 16px; }
  .plaque .presents { display: block; font-size: 22px; line-height: 28px; margin-top: 2px; }
  .title-block {
    position: absolute; text-align: center; white-space: nowrap;
    font-family: "Sancreek", serif; font-weight: 400; color: var(--cream); background: var(--ink);
  }
  .title-nouveau { top: 412px; left: 255px; width: 339px; height: 94px; font-size: 72px; line-height: 94px; }
  .title-cirque { top: 506px; left: 160px; width: 529px; height: 178px; font-size: 144px; line-height: 178px; }
  .event-line, .date-line {
    position: absolute; left: 0; right: 0; text-align: center; white-space: nowrap;
    font-family: "Cinzel", serif; font-weight: 900; color: var(--cream);
    -webkit-text-stroke: 1.5px var(--ink); paint-order: stroke fill;
    text-shadow: 2px 2px 0 var(--ink);
  }
  .event-line { top: 772px; font-size: 42px; line-height: 46px; }
  .date-line { top: 990px; font-size: 30px; line-height: 34px; color: #f3e0b0; }
  .web {
    position: absolute; left: 0; right: 0; top: 1034px; text-align: center; white-space: nowrap;
    font-family: "Arimo", sans-serif; font-weight: 700; font-size: 26px; line-height: 30px; color: var(--cream);
  }
  .sponsor-strip { position: absolute; left: 94px; right: 94px; top: 1088px; height: 73px;
    background: var(--strip); border-radius: 22px; }
</style>
</head>
<body>
<main class="poster">
  <div class="fill side-pattern left" role="img" aria-label="Floral vintage wallpaper pattern"></div>
  <div class="fill side-pattern right" role="img" aria-label="Floral vintage wallpaper pattern"></div>
  <div class="fill stage-panel"></div>
  <div class="fill crest" role="img" aria-label="Ornate crest with crown and scrollwork"></div>
  <div class="fill curtain" role="img" aria-label="Red stage curtain drawn open"></div>
  <div class="fill figure left" role="img" aria-label="Circus performer in red costume"></div>
  <div class="fill figure right" role="img" aria-label="Circus performer in red costume"></div>

  <svg class="frame-lines" width="849" height="1200" viewBox="0 0 849 1200" aria-hidden="true">
    <rect x="10" y="10" width="829" height="1180" fill="none" stroke="#7a4a1c" stroke-width="3"/>
    <rect x="58" y="58" width="733" height="1102" fill="none" stroke="#f1ddb0" stroke-width="4"/>
    <line x1="72" y1="58" x2="72" y2="1160" stroke="#f1ddb0" stroke-width="2"/>
    <line x1="777" y1="58" x2="777" y2="1160" stroke="#f1ddb0" stroke-width="2"/>
    <path d="M150 170 Q424 -40 699 170" fill="none" stroke="#f1ddb0" stroke-width="4"/>
  </svg>

  <div class="plaque">
    <span class="host">QUILLMERE GALA</span>
    <span class="presents">PROUDLY PRESENTS</span>
  </div>

  <h1>
    <span class="title-block title-nouveau">NOUVEAU</span>
    <span class="title-block title-cirque">CIRQUE</span>
  </h1>

  <p class="event-line">2011 NEW YEARS EVE<br>EXTRAVAGANZA</p>
  <p class="date-line">SATURDAY 31ST DECEMBER</p>
  <p class="web">WWW.QUILLMEREGALA-EXAMPLE.COM</p>

  <div class="sponsor-strip"></div>
</main>
</body>
</html>
```